Business card design for Brivo Engineering Tandem

We need a new business card design along with all the necessary to place an order. The company is Brivo Engineering Tandem and we recently updated our logo.

```html
<!DOCTYPE html>
<html lang="en">
<head>
<meta charset="utf-8">
<title>Brivo Engineering Tandem – Business Card</title>
<link href="https://fonts.googleapis.com/css2?family=Montserrat:wght@400;500;600;700&display=swap" rel="stylesheet">
<style>
  :root {
    --page: #e4e4e4;
    --card: #ffffff;
    --brand-grey: #8f8f8f;
    --band-grey: #9a9a9a;
    --brand-yellow: #e2bd1f;
    --ink: #1f1f1f;
    --shadow: rgba(0,0,0,0.18);
  }
  * { box-sizing: border-box; margin: 0; padding: 0; }
  html, body {
    width: 1200px; height: 874px; overflow: hidden;
    background: var(--page);
    font-family: "Montserrat", sans-serif;
  }
  .sheet {
    position: relative; width: 1200px; height: 874px;
    display: flex; flex-direction: column; align-items: center; justify-content: center; gap: 40px;
  }
  .card {
    position: relative; width: 640px; height: 366px;
    background: var(--card); border-radius: 18px; overflow: hidden;
    box-shadow: 0 10px 28px var(--shadow);
  }
  .card-band { position: absolute; left: 0; bottom: 0; width: 640px; height: 24px; display: block; }

  /* front */
  .front-wordmark {
    position: absolute; inset: 0 0 24px 0;
    display: flex; align-items: center; justify-content: center; gap: 14px;
  }
  .brand-square { width: 22px; height: 22px; background: var(--brand-yellow); flex: none; }
  .brand-name {
    color: var(--brand-grey); font-weight: 600; text-transform: uppercase;
    letter-spacing: 0.04em; line-height: 1.1;
  }
  .front-wordmark .brand-name { font-size: 30px; }

  /* back */
  .back-layout {
    position: absolute; inset: 0 0 24px 0;
    display: flex; align-items: center; padding-left: 36px;
  }
  .back-wordmark { display: flex; align-items: center; gap: 10px; width: 226px; }
  .back-wordmark .brand-square { width: 14px; height: 14px; }
  .back-wordmark .brand-name { font-size: 17px; }
  .divider { width: 2px; height: 160px; background: var(--brand-yellow); margin: 0 22px 0 10px; }
  .contact { color: var(--ink); }
  .contact-name { color: var(--brand-yellow); font-weight: 700; font-size: 23px; line-height: 1.1; }
  .contact-role { font-size: 14px; font-weight: 500; margin-bottom: 8px; }
  .contact-address { font-size: 14px; line-height: 1.35; margin-bottom: 8px; }
  .contact-list { list-style: none; font-size: 14px; line-height: 1.7; }
  .contact-list li { display: flex; align-items: center; gap: 8px; }
  .contact-list svg { width: 12px; height: 12px; flex: none; }
</style>
</head>
<body>
<main class="sheet">

  <section class="card card-front" aria-label="Card front">
    <div class="front-wordmark">
      <span class="brand-square"></span>
      <span class="brand-name">Brivo Engineering Tandem</span>
    </div>
    <svg class="card-band" viewBox="0 0 640 24" preserveAspectRatio="none" aria-hidden="true">
      <polygon points="0,0 300,0 280,24 0,24" fill="var(--band-grey)"/>
      <polygon points="310,0 640,0 640,24 290,24" fill="var(--brand-yellow)"/>
    </svg>
  </section>

  <section class="card card-back" aria-label="Card back">
    <div class="back-layout">
      <div class="back-wordmark">
        <span class="brand-square"></span>
        <span class="brand-name">Brivo<br>Engineering<br>Tandem</span>
      </div>
      <div class="divider"></div>
      <div class="contact">
        <p class="contact-name">Marcus Delgado</p>
        <p class="contact-role">Managing Director</p>
        <p class="contact-address">48 Foundry Lane<br>Ashby, OR 97410 USA</p>
        <ul class="contact-list">
          <li>
            <svg viewBox="0 0 12 12" aria-hidden="true"><path d="M2.5 1 L4.5 1 L5 3.5 L3.8 4.4 C4.5 6 6 7.5 7.6 8.2 L8.5 7 L11 7.5 L11 9.5 C11 10.3 10.3 11 9.5 11 C5 11 1 7 1 2.5 C1 1.7 1.7 1 2.5 1 Z" fill="var(--brand-yellow)"/></svg>
            (541)555-0172
          </li>
          <li>
            <svg viewBox="0 0 12 12" aria-hidden="true"><rect x="0.5" y="2" width="11" height="8" fill="var(--brand-yellow)"/><path d="M0.5 2 L6 6.5 L11.5 2" stroke="#fff" stroke-width="1" fill="none"/></svg>
            info@brivotandem.com
          </li>
          <li>
            <svg viewBox="0 0 12 12" aria-hidden="true"><circle cx="6" cy="6" r="5.2" fill="var(--brand-yellow)"/><path d="M0.8 6 H11.2 M6 0.8 C3.5 3.5 3.5 8.5 6 11.2 M6 0.8 C8.5 3.5 8.5 8.5 6 11.2" stroke="#fff" stroke-width="0.8" fill="none"/></svg>
            www.brivotandem.com
          </li>
        </ul>
      </div>
    </div>
    <svg class="card-band" viewBox="0 0 640 24" preserveAspectRatio="none" aria-hidden="true">
      <polygon points="0,0 300,0 280,24 0,24" fill="var(--band-grey)"/>
      <polygon points="310,0 640,0 640,24 290,24" fill="var(--brand-yellow)"/>
    </svg>
  </section>

</main>
</body>
</html>
```